Redesign This Psychology Website

We would like a slight redesign of this successful psychology (relationship counselling) website:

www.TheKelvaleClinic.com.au

We are updating the website, and we'd like a slight refresh of the design and style.

Please keep to very similar colours, and use the same logo. We're looking for around 10 page templates, however the main one is the home page.

Keep in mind, this website already converts quite well, so we want a new, fresh design in keeping with this one. Please don't bother designing something too extremely different.

thanks :)

Target Market(s)

couples who are looking for relationship counselling. Men and women, 25 - 70, across Australia

Industry/Entity Type

Psychology

Number of Pages Required

5+ page

Font styles to use
Sans Serif

Colors
87cfc6
b7a5cd
ec1f27
ffffff
cee9f5

Requirements
Must have
• a similar look to the current design, just looking for a slight refresh.
• Search bar
• Areas for lots of photos
• same logo
• lots of content areas
Nice to have
• great content areas, where we can display a lot of content and our areas.
Should not have
• no colors like orange, etc.
• should not have a totally different feel.

```html
<!DOCTYPE html>
<html lang="en">
<head>
<meta charset="utf-8">
<title>About Us – The Kelvale Clinic</title>
<link href="https://fonts.googleapis.com/css2?family=Nunito+Sans:wght@400;600;700;800&family=Open+Sans:wght@400;600;700&display=swap" rel="stylesheet">
<style>
:root{
  --teal:#87cfc6;
  --teal-deep:#3ea7a0;
  --teal-dark:#2f7f86;
  --purple:#b7a5cd;
  --purple-deep:#8f7bb0;
  --red:#ec1f27;
  --sky:#cee9f5;
  --ink:#333;
  --text:#6b6b6b;
  --line:#dcdcdc;
  --paper:#fff;
  --mist:#f3f3f3;
}
*{box-sizing:border-box;margin:0;padding:0}
html,body{width:1200px;height:3974px;overflow:hidden;background:var(--paper)}
body{position:relative;font-family:"Open Sans",Arial,sans-serif;color:var(--text)}

.topbar{position:absolute;left:0;top:0;width:1200px;height:37px;background:var(--mist);border-bottom:1px solid #e6e6e6;font-size:13px}
.topbar .associate{position:absolute;left:132px;top:10px;color:#777}
.topbar .util{position:absolute;right:132px;top:10px;display:flex;color:#777}
.topbar .util span{padding:0 10px;border-left:1px solid #ccc}
.topbar .util span:first-child{border-left:0}

.masthead{position:absolute;left:0;top:37px;width:1200px;height:123px}
.brand{position:absolute;left:132px;top:38px;display:flex;align-items:center;gap:12px}
.brand-dot{width:40px;height:40px;border-radius:50%;background:var(--teal-deep)}
.brand-name{font-family:"Open Sans",sans-serif;font-weight:700;font-size:28px;color:var(--teal-dark);line-height:1}
.search{position:absolute;left:472px;top:50px;width:291px;height:32px;border:1px solid #cfcfcf;border-radius:3px;display:flex;align-items:center;padding-left:10px;gap:8px;font-size:13px;color:#999}
.call{position:absolute;right:132px;top:36px;text-align:right;font-family:"Nunito Sans",sans-serif}
.call .label{color:var(--teal);font-size:16px}
.call .number{color:var(--red);font-size:27px;font-weight:700;display:flex;align-items:center;gap:6px}

.mainnav{position:absolute;left:0;top:160px;width:1200px;height:73px;background:linear-gradient(#a2ddd5,#7ec8be)}
.mainnav ul{list-style:none;position:absolute;left:132px;width:938px;height:73px;display:flex;justify-content:space-between;align-items:center}
.mainnav li{font-family:"Nunito Sans",sans-serif;font-weight:700;color:#fff;font-size:15px;text-transform:uppercase;text-align:center;line-height:1.15;padding:0 12px;border-left:1px solid rgba(255,255,255,.6)}
.mainnav li:first-child{border-left:0;padding-left:0}
.mainnav li:last-child{padding-right:0}

.hero{position:absolute;left:0;top:233px;width:1200px;height:323px;background:linear-gradient(100deg,#6e625c 0%,#9a8f8a 35%,#c9bdb5 55%,#5a4a45 78%,#3c302d 100%)}
.hero h1{position:absolute;left:127px;top:166px;color:#fff;font-family:"Nunito Sans",sans-serif;font-weight:700;font-size:38px;letter-spacing:.5px}

.intro{position:absolute;left:127px;top:606px;width:620px}
.intro h2{font-family:"Nunito Sans",sans-serif;font-weight:600;font-size:29px;line-height:1.2;color:var(--ink);margin-bottom:18px}
.intro p{font-size:13.5px;line-height:1.65;margin-bottom:13px}

.section-title{position:absolute;left:127px;top:1074px;font-family:"Nunito Sans",sans-serif;font-size:28px;color:var(--red);font-weight:600}

.psych{position:absolute;left:127px;width:620px;display:flex;gap:14px}
.psych .portrait{flex:0 0 125px;height:125px;border-radius:50%;background:radial-gradient(circle at 50% 40%,#d8c0a8,#8a6f5c)}
.psych .info{flex:1}
.psych h3{font-family:"Nunito Sans",sans-serif;font-size:22px;font-weight:600;color:var(--teal-deep);margin-bottom:4px}
.psych .role{font-size:12.5px;color:#555;line-height:1.55}
.psych .cert{font-size:12.5px;color:var(--teal-dark);font-weight:600;line-height:1.55}
.psych .bio{font-size:12.5px;line-height:1.55;margin:2px 0 12px}
.psych .actions{display:flex;align-items:center;gap:14px}
.btn-outline{border:1px solid var(--purple);color:var(--purple-deep);font-size:12px;padding:6px 18px;border-radius:2px;letter-spacing:.5px}
.book{font-size:12px;font-weight:700;color:#444}

.finder{position:absolute;left:765px;top:599px;width:303px;height:368px;background:var(--purple);padding:26px 26px}
.finder h4{font-family:"Nunito Sans",sans-serif;color:#fff;font-size:24px;font-weight:700;text-align:center;line-height:1.2}
.finder .rule{display:flex;align-items:center;gap:10px;justify-content:center}
.finder .rule::before,.finder .rule::after{content:"";width:32px;height:1px;background:#fff}
.finder label{display:block;color:#fff;font-size:13px;margin:14px 0 4px}
.finder .field{height:30px;background:#fff;font-size:12px;color:#888;padding:7px 8px}
.finder .go{margin-top:18px;height:36px;background:var(--red);color:#fff;font-weight:700;font-size:15px;text-align:center;line-height:36px}

.promo{position:absolute;left:765px;width:303px;height:240px;border:1px solid var(--line);display:flex;overflow:hidden}
.promo .copy{width:150px;padding:22px 0 0 22px}
.promo h5{font-family:"Nunito Sans",sans-serif;font-size:21px;font-weight:600;color:var(--ink);line-height:1.2;margin-bottom:8px}
.promo p{font-size:11px;line-height:1.5;color:#888;margin-bottom:12px}
.promo .learn{display:inline-block;background:var(--purple-deep);color:#fff;font-size:10px;padding:5px 12px}
.promo .photo{flex:1}

.article{position:absolute;left:776px;width:292px;height:115px;border:1px solid var(--line);display:flex;background:#fff}
.article .thumb{flex:0 0 135px}
.article .txt{padding:14px 10px 0 14px}
.article h6{font-family:"Nunito Sans",sans-serif;font-size:15px;font-weight:600;color:var(--ink);line-height:1.25}
.article .more{font-size:12px;color:var(--teal-deep);margin-top:4px}

.footer{position:absolute;left:0;top:3603px;width:1200px;height:291px;background:linear-gradient(#f0f0f0,#fbfbfb)}
.footer .brand{top:100px}
.fcol{position:absolute;top:72px;font-size:13px;line-height:1.9;color:#777}
.fcol h5{font-family:"Nunito Sans",sans-serif;font-weight:800;font-size:16px;color:var(--teal-deep);text-transform:uppercase;margin-bottom:6px}
.social{display:flex;gap:6px;margin-top:6px}
.social span{width:28px;height:28px;border-radius:50%}
.legal{position:absolute;left:0;top:3894px;width:1200px;height:80px;background:#e9e9e9;text-align:center;line-height:80px;font-size:13px;color:#888}
</style>
</head>
<body>

<div class="topbar">
  <div class="associate">Join Our Associate Program →</div>
  <div class="util"><span>Home</span><span>Cart</span><span>Blog</span><span>Resources</span><span>Contact</span></div>
</div>

<header class="masthead">
  <div class="brand">
    <span class="brand-dot"></span>
    <div class="brand-name">The Kelvale Clinic</div>
  </div>
  <div class="search">
    <svg width="14" height="14" viewBox="0 0 14 14"><circle cx="6" cy="6" r="4.5" fill="none" stroke="#999" stroke-width="1.5"/><line x1="9.3" y1="9.3" x2="13" y2="13" stroke="#999" stroke-width="1.5"/></svg>
    Search here
  </div>
  <div class="call">
    <div class="label">Call Us Now</div>
    <div class="number">
      <svg width="22" height="22" viewBox="0 0 24 24"><path d="M6.6 10.8a15 15 0 0 0 6.6 6.6l2.2-2.2c.3-.3.7-.4 1-.2 1.1.4 2.3.6 3.6.6.6 0 1 .4 1 1V20c0 .6-.4 1-1 1A17 17 0 0 1 3 4c0-.6.4-1 1-1h3.5c.6 0 1 .4 1 1 0 1.3.2 2.5.6 3.6.1.3 0 .7-.2 1z" fill="none" stroke="#ec1f27" stroke-width="1.8"/></svg>
      1300 417 286
    </div>
  </div>
</header>

<nav class="mainnav">
  <ul>
    <li>Counselling<br>Types</li>
    <li>Relationship Counselling<br>Locations</li>
    <li>Sex Therapy<br>Locations</li>
    <li>About Us</li>
    <li>Quizzes</li>
    <li>FAQ's</li>
    <li>Contact</li>
  </ul>
</nav>

<section class="hero" role="img" aria-label="Photo of a couple lying together on a soft rug">
  <h1>ABOUT US</h1>
</section>

<section class="intro">
  <h2>The Kelvale Clinic is a company passionate about creating healthy loving relationships, of all kinds.</h2>
  <p>Our mission is to be the most highly regarded relationship help service in Australia, by delivering a comprehensive range of the highest quality relationship and marriage counselling and advice, and books and products to educate and enhance client's relationships. To have every client who comes through our doors leave feeling listened to, understood, and educated on how to build a better relationship with their partner, while at the same time bringing out the best in themselves.</p>
  <p>We have been in operation for 16 years in Australia.</p>
  <p>Our counsellors are all Psychologists, and in addition, we have our own in-house relationship counselling training program, and ongoing professional development program, and are constantly seeking best practice methodologies.</p>
  <p>With our specialized experience in relationship and marriage counselling, together with our caring, compassionate and unbiased approach, you are in safe and experienced hands.</p>
</section>

<h2 class="section-title">Our Psychologists</h2>

<article class="psych" style="top:1126px">
  <div class="portrait" role="img" aria-label="Portrait photo of a psychologist"></div>
  <div class="info">
    <h3>Leonie</h3>
    <div class="role">Registered Psychologist Sydney</div>
    <div class="role">BA (Psych); Grad Dip (Psych); Grad Dip (Rel Couns &amp; Fam Therapy)</div>
    <div class="cert">Kelvale Clinic Certified</div>
    <p class="bio">Leonie is a registered psychologist and qualified relationship and family counsellor since 2006. She has worked for not-for-profit organisations and the community sector for over twenty years. Leonie sees individuals, couples and families, and is also an approved insurance provider.</p>
    <div class="actions"><span class="btn-outline">READ MORE</span><span class="book">Or to book an appointment, please call 1300 417 286</span></div>
  </div>
</article>

<article class="psych" style="top:1412px">
  <div class="portrait" role="img" aria-label="Portrait photo of a psychologist"></div>
  <div class="info">
    <h3>Harriet</h3>
    <div class="role">Registered Psychologist Sydney</div>
    <div class="role">BA (Psych), Grad Dip Sc (Psych), Grad Dip (App Psych), MA (Coaching Psychology)</div>
    <div class="cert">Kelvale Clinic Certified</div>
    <p class="bio">Harriet has specialised in individual and relationship counselling in Sydney and has worked as a psychologist for over 12 years in a variety of public and private settings. She has also worked as a college guidance counsellor with children, teenagers and their families, and understands the busy lifestyles many families lead today. Video and phone sessions are available if face to face sessions are not possible.</p>
    <div class="actions"><span class="btn-outline">READ MORE</span><span class="book">Or to book an appointment, please call 1300 417 286</span></div>
  </div>
</article>

<article class="psych" style="top:1735px">
  <div class="portrait" role="img" aria-label="Portrait photo of a psychologist"></div>
  <div class="info">
    <h3>Rosalind</h3>
    <div class="role">Registered Psychologist Sydney</div>
    <div class="role">BA (Psych); Grad Dip (Psych); Grad Dip (Rel Couns &amp; Fam Therapy)</div>
    <div class="cert">Kelvale Clinic Certified</div>
    <p class="bio">Rosalind is a registered psychologist and qualified relationship and family counsellor since 2006. She has worked for not-for-profit organisations and the community sector for over twenty years. Rosalind sees individuals, couples and families, and is also an approved insurance provider.</p>
    <div class="actions"><span class="btn-outline">READ MORE</span><span class="book">Or to book an appointment, please call 1300 417 286</span></div>
  </div>
</article>

<article class="psych" style="top:2018px">
  <div class="portrait" role="img" aria-label="Portrait photo of a psychologist"></div>
  <div class="info">
    <h3>Yvonne</h3>
    <div class="role">Registered Psychologist Melbourne</div>
    <div class="role">B.Psych (Hons 1st), B.App.Sci. (Health Sci Hons 1st)</div>
    <div class="cert">Kelvale Clinic Certified</div>
    <p class="bio">Yvonne is passionate about couples counselling. Her sincere and genuine desire to assist individuals and couples in creating stronger, healthier and more satisfying relationships has been her guiding motivation for almost two decades of working in the field of relationship psychology. Described by both clients and colleagues as warm, open, personable and compassionate, her relaxed style promotes a comfortable, safe environment to explore relationship issues.</p>
    <div class="actions"><span class="btn-outline">READ MORE</span><span class="book">Or to book an appointment, please call 1300 417 286</span></div>
  </div>
</article>

<article class="psych" style="top:2344px">
  <div class="portrait" role="img" aria-label="Portrait photo of a counsellor"></div>
  <div class="info">
    <h3>Marlene</h3>
    <div class="role">Diploma in Counselling</div>
    <div class="cert">Kelvale Clinic Certified</div>
    <p class="bio">Marlene provides marriage counselling in Sydney and holds a Diploma of Counselling, along with being trained through the clinic in the development of complex counselling skills. She is a member of a national counselling body and participates in reflective individual and peer clinical supervision on a regular basis, keeping her practice current and caring.</p>
    <div class="actions"><span class="btn-outline">READ MORE</span><span class="book">Or to book an appointment, please call 1300 417 286</span></div>
  </div>
</article>

<article class="psych" style="top:2636px">
  <div class="portrait" role="img" aria-label="Portrait photo of a psychologist"></div>
  <div class="info">
    <h3>Tamsin</h3>
    <div class="role">Registered Psychologist Brisbane</div>
    <div class="role">B Soc Work; B Ed (Hons); B Soc Sci (Psych); Grad Dip Psych; Grad Dip Couns; M Couns</div>
    <div class="cert">Kelvale Clinic Certified</div>
    <p class="bio">Tamsin is passionate about individual and relationship counselling and believes it is an honour and privilege to be allowed to hear somebody's life story. Her experience has involved working with families, couples and individuals dealing with challenging life events such as illness, loss and grief, and with women, young people and children who have faced hardship.</p>
    <div class="actions"><span class="btn-outline">READ MORE</span><span class="book">Or to book an appointment, please call 1300 417 286</span></div>
  </div>
</article>

<article class="psych" style="top:2962px">
  <div class="portrait" role="img" aria-label="Portrait photo of a counsellor"></div>
  <div class="info">
    <h3>Bronwyn</h3>
    <div class="role">Registered Counsellor</div>
    <div class="role">B Psych (Hons); Grad Dip Rel Couns</div>
    <div class="cert">Kelvale Clinic Certified</div>
    <p class="bio">Bronwyn provides marriage counselling in Sydney, and has an Honours Degree in Psychology and a Graduate Diploma of Relationship Counselling. She is also clinic certified and a registered member of a national counselling body. She engages in regular self-reflection and participates in peer and clinical supervision to support the couples she sees.</p>
    <div class="actions"><span class="btn-outline">READ MORE</span><span class="book">Or to book an appointment, please call 1300 417 286</span></div>
  </div>
</article>

<article class="psych" style="top:3264px">
  <div class="portrait" role="img" aria-label="Portrait photo of a psychologist"></div>
  <div class="info">
    <h3>Isabella</h3>
    <div class="role">Registered Psychologist Sydney</div>
    <div class="role">B Psych (Hons); Grad Dip Int Comm; PhD</div>
    <div class="cert">Kelvale Clinic Certified</div>
    <p class="bio">Dr Isabella is a registered psychologist in Sydney and a full member of the national psychological society. She specialises in couples counselling and marriage preparation. In addition to her Honours Degree in Psychology, she holds a PhD and a Postgraduate Diploma in Intercultural Communication. She has worked as a psychologist in private, academic and corporate settings.</p>
    <div class="actions"><span class="btn-outline">READ MORE</span><span class="book">Or to book an appointment, please call 1300 417 286</span></div>
  </div>
</article>

<aside class="finder">
  <h4>Find Our Psychologist</h4>
  <h4 class="rule">Near You</h4>
  <label>Type of Counselling</label>
  <div class="field">Select</div>
  <label>Location</label>
  <div class="field"></div>
  <label>Postcode</label>
  <div class="field"></div>
  <div class="go">SEARCH</div>
</aside>

<div class="promo" style="top:985px">
  <div class="copy"><h5>Rebates<br>Available</h5><p>Claim part of your session fee back through your health fund.</p><span class="learn">Learn More</span></div>
  <div class="photo" role="img" aria-label="Photo of hands holding a health card" style="background:linear-gradient(90deg,#fff,#e8c9cf 35%,#b98a96)"></div>
</div>
<div class="promo" style="top:1245px">
  <div class="copy"><h5>GP Referral<br>Info</h5><p>Ask your doctor about a mental health care plan today.</p><span class="learn">Learn More</span></div>
  <div class="photo" role="img" aria-label="Photo of a doctor" style="background:linear-gradient(90deg,#fff,#e4eef3 35%,#a9c3cf)"></div>
</div>
<div class="promo" style="top:1510px">
  <div class="copy"><h5>Anxiety and<br>Depression</h5><p>Support to feel calmer and more hopeful about life.</p><span class="learn">Learn More</span></div>
  <div class="photo" role="img" aria-label="Photo of a worried man" style="background:linear-gradient(90deg,#fff,#8c8c8c 30%,#3a3a3a)"></div>
</div>

<div class="article" style="top:1770px"><div class="thumb" role="img" aria-label="Photo of two hands reaching" style="background:linear-gradient(135deg,#c9a58c,#7d6152)"></div><div class="txt"><h6>What can I do if I'm living with a Narcissist?</h6><div class="more">Read More</div></div></div>
<div class="article" style="top:1898px"><div class="thumb" role="img" aria-label="Photo of a tense couple" style="background:linear-gradient(135deg,#7a6a60,#2f2824)"></div><div class="txt"><h6>Are You Living With a Steamroller?</h6><div class="more">Read More</div></div></div>
<div class="article" style="top:2026px"><div class="thumb" role="img" aria-label="Photo of a couple in conversation" style="background:linear-gradient(135deg,#b8a191,#4e3f38)"></div><div class="txt"><h6>Did Your Relationship Start on Rocky Ground?</h6><div class="more">Read More</div></div></div>
<div class="article" style="top:2166px"><div class="thumb" role="img" aria-label="Photo of a woman looking away" style="background:linear-gradient(135deg,#e2d6cc,#a48d7e)"></div><div class="txt"><h6>Why am I with a Narcissist?</h6><div class="more">Read More</div></div></div>
<div class="article" style="top:2293px"><div class="thumb" role="img" aria-label="Photo of a couple sitting apart" style="background:linear-gradient(135deg,#d5c6bb,#8e7a6d)"></div><div class="txt"><h6>Letter for a Partner Doubtful About Relationship Counselling</h6><div class="more">Read More</div></div></div>
<div class="article" style="top:2426px"><div class="thumb" role="img" aria-label="Photo of a couple together" style="background:linear-gradient(135deg,#cdb39f,#6f5647)"></div><div class="txt"><h6>What Are You Like In a Relationship?</h6><div class="more">Read More</div></div></div>
<div class="article" style="top:2553px"><div class="thumb" role="img" aria-label="Photo of a couple embracing" style="background:linear-gradient(135deg,#9c8577,#3a2c25)"></div><div class="txt"><h6>How Do I Know If I'm With a Narcissist?</h6><div class="more">Read More</div></div></div>
<div class="article" style="top:2686px"><div class="thumb" role="img" aria-label="Photo of a couple outdoors" style="background:linear-gradient(135deg,#d7cabf,#8b7566)"></div><div class="txt"><h6>Do You Wonder Why You and Your Partner Are Together?</h6><div class="more">Read More</div></div></div>
<div class="article" style="top:2813px"><div class="thumb" role="img" aria-label="Photo of a businessman at work" style="background:linear-gradient(135deg,#b5aaa3,#4a4340)"></div><div class="txt"><h6>Is Your Pursuit of Success Sabotaging Your Relationships That Matter Most?</h6><div class="more">Read More</div></div></div>

<footer class="footer">
  <div class="brand">
    <span class="brand-dot"></span>
    <div class="brand-name">The Kelvale Clinic</div>
  </div>
  <div class="fcol" style="left:463px">
    <h5>Quick Links</h5>
    Home<br>About Us<br>Our Blogs<br>Shop Cart<br>Contact Us
  </div>
  <div class="fcol" style="left:630px">
    <h5>Resources</h5>
    Counselling Type<br>Sex Therapy<br>Quizzes<br>FAQ<br>Relationship Counselling
  </div>
  <div class="fcol" style="left:834px">
    <h5>Contact Us</h5>
    41 Harbour Lane Suite 210<br>1300 417 286<br>Email: info@companyname.com
    <div class="social">
      <span style="background:#4fb6e6"></span><span style="background:#3b5a9a"></span><span style="background:#2a7ab0"></span><span style="background:#dd4b39"></span>
    </div>
  </div>
</footer>
<div class="legal">© 2017 Company Name. All right reserved</div>

</body>
</html>
```